Biz cards, stationary, envelopes for Bright Hollow Church
Bright Hollow Church marketing package
Designers,
Thank all of you for your creativity and your contributions to this project. As our first project we are well pleased with the outcome and look forward to seeing you on future projects we post in the future.
Best wishes...
RW
Designers,just wanted to say all of you have submitted amazing drafts! For finalization, would like the "P" in logo to be the same brown color as "church." Some of you have already done so but this brings some consistency to the cards. Again nice designs! RW
KT/FRN/DV Team
Designers, can we have an option 2 for the back of the card under logo to read: 2 Cor. 5:18-20 (bold). Also please write "Church" in sentence case. Nice designs!!

```html
<!DOCTYPE html>
<html lang="en">
<head>
<meta charset="utf-8">
<title>Bright Hollow Church Stationery</title>
<link href="https://fonts.googleapis.com/css2?family=Open+Sans:wght@400;600;700&display=swap" rel="stylesheet">
<style>
:root{
  --bg:#ece6dc;
  --paper:#ffffff;
  --navy:#0d2a6b;
  --blue:#1f58b4;
  --sky:#5f9be0;
  --gold:#e8b80c;
  --gold-dark:#b88600;
  --brown:#6b3b1f;
  --ink:#333333;
  --rule:#9a9a9a;
  --faint:#eef2f8;
}
*{box-sizing:border-box;margin:0;padding:0}
html,body{width:1200px;height:674px;overflow:hidden}
body{background:var(--bg);font-family:"Open Sans",Arial,sans-serif;color:var(--ink);position:relative}
.piece{position:absolute;background:var(--paper);box-shadow:0 2px 6px rgba(0,0,0,.25);overflow:hidden}
.label{position:absolute;font-size:7px;font-weight:600;color:#222;text-align:center;white-space:nowrap}
.brand{display:flex;align-items:center;gap:4px;position:absolute}
.brand-mark{border-radius:50%;background:var(--blue);flex:none}
.brand-name{font-weight:700;color:var(--brown);line-height:1.05}
.contact{position:absolute;font-size:5px;line-height:1.45;color:var(--ink);text-align:left}
.swoosh{position:absolute;left:0;bottom:0;width:100%}
.faint-circle{position:absolute;border-radius:50%;border:14px solid var(--faint)}
.web{position:absolute;font-size:4.5px;color:#fff;right:10px}

/* business cards */
.card{width:110px;height:68px;top:50px}
.card-back{display:flex;align-items:center;justify-content:center}
.card-back.blue{background:radial-gradient(circle at 50% 45%,var(--sky),var(--blue) 55%,var(--navy))}
.card-back.gold{background:radial-gradient(circle at 50% 45%,#ffe680,var(--gold) 55%,var(--gold-dark))}
.card-back .brand{position:static}

/* fax */
.fax-title{position:absolute;right:14px;top:86px;font-size:9px;font-weight:700;color:var(--navy)}
.fax-table{position:absolute;left:14px;top:98px;width:312px;border-collapse:collapse;font-size:6px}
.fax-table td{border:1px solid var(--rule);height:17px;padding:0 3px}
.fax-table td.key{width:38px;font-weight:600}
.fax-checks{position:absolute;left:14px;top:180px;display:flex;gap:14px;font-size:5.5px}
.fax-checks span::before{content:"";display:inline-block;width:5px;height:5px;border:1px solid var(--rule);margin-right:3px;vertical-align:-1px}

/* envelopes */
.env-back{width:413px;height:140px;left:763px;background:var(--paper)}
.env-label{position:absolute;width:100%;text-align:center;top:36px;font-size:7px;font-weight:600;color:#222}
</style>
</head>
<body>

<!-- Business cards -->
<div class="label" style="left:29px;top:36px;width:110px">Business Card (Front)</div>
<div class="piece card" style="left:29px">
  <div class="brand" style="left:6px;top:9px">
    <div class="brand-mark" style="width:14px;height:14px"></div>
    <div class="brand-name" style="font-size:5.5px">Bright Hollow<br>Church</div>
  </div>
  <div class="contact" style="left:6px;top:30px;font-size:4px">PO Box 218<br>Millbrook, TX 75400<br>T 555 010 2200<br>info@brighthollowchurch.org</div>
  <svg class="swoosh" viewBox="0 0 110 16" height="16" preserveAspectRatio="none"><path d="M0 10 Q55 0 110 6 L110 16 L0 16Z" fill="var(--gold)"/><path d="M0 13 Q55 4 110 9 L110 16 L0 16Z" fill="var(--blue)"/></svg>
</div>

<div class="label" style="left:163px;top:36px;width:110px">Business Card (Back) Option 1</div>
<div class="piece card card-back" style="left:163px">
  <div class="brand"><div class="brand-mark" style="width:16px;height:16px"></div><div class="brand-name" style="font-size:6px">Bright Hollow<br>Church</div></div>
  <svg class="swoosh" viewBox="0 0 110 14" height="14" preserveAspectRatio="none"><path d="M0 9 Q55 0 110 5 L110 14 L0 14Z" fill="var(--gold)"/><path d="M0 12 Q55 3 110 8 L110 14 L0 14Z" fill="var(--blue)"/></svg>
</div>

<div class="label" style="left:293px;top:36px;width:110px">Business Card (Back) Option 2</div>
<div class="piece card card-back blue" style="left:293px">
  <div class="brand"><div class="brand-mark" style="width:16px;height:16px;background:#fff"></div><div class="brand-name" style="font-size:6px;color:#fff">Bright Hollow<br>Church</div></div>
</div>

<div class="label" style="left:427px;top:36px;width:110px">Business Card (Back) Option 3</div>
<div class="piece card card-back gold" style="left:427px">
  <div class="brand"><div class="brand-mark" style="width:16px;height:16px"></div><div class="brand-name" style="font-size:6px">Bright Hollow<br>Church</div></div>
</div>

<!-- Envelope front -->
<div class="label" style="left:653px;top:36px;width:172px">Envelope (Front)</div>
<div class="piece" style="left:653px;top:50px;width:172px;height:80px">
  <div class="brand" style="left:7px;top:7px">
    <div class="brand-mark" style="width:13px;height:13px"></div>
    <div class="brand-name" style="font-size:5px">Bright Hollow<br>Church</div>
  </div>
  <div class="contact" style="left:7px;top:25px;font-size:4px">PO Box 218<br>Millbrook, TX 75400</div>
  <svg class="swoosh" viewBox="0 0 172 12" height="12" preserveAspectRatio="none"><path d="M0 8 Q86 0 172 5 L172 12 L0 12Z" fill="var(--gold)"/><path d="M0 10 Q86 3 172 8 L172 12 L0 12Z" fill="var(--blue)"/></svg>
  <div class="web" style="bottom:2px;font-size:3.5px">www.brighthollowchurch.org</div>
</div>

<!-- Fax cover -->
<div class="label" style="left:29px;top:143px;width:343px">Fax Cover</div>
<div class="piece" style="left:29px;top:156px;width:343px;height:492px">
  <div class="faint-circle" style="left:96px;top:200px;width:150px;height:150px"></div>
  <div class="brand" style="left:14px;top:14px">
    <div class="brand-mark" style="width:24px;height:24px"></div>
    <div class="brand-name" style="font-size:8px">Bright Hollow<br>Church</div>
  </div>
  <div class="contact" style="left:262px;top:14px">PO Box 218<br>Millbrook, TX 75400<br>T 555 010 2200<br>F 555 010 2201<br>info@brighthollowchurch.org</div>
  <div class="fax-title">FAX</div>
  <table class="fax-table">
    <tr><td class="key">To:</td><td></td><td class="key">Date:</td><td></td></tr>
    <tr><td class="key">From:</td><td></td><td class="key">Pages:</td><td></td></tr>
    <tr><td class="key">Phone:</td><td></td><td class="key">CC:</td><td></td></tr>
    <tr><td class="key">Re:</td><td></td><td class="key">Fax:</td><td></td></tr>
  </table>
  <div class="fax-checks"><span>Urgent</span><span>For Review</span><span>Please Comment</span><span>Please Reply</span><span>Please Recycle</span></div>
  <svg class="swoosh" viewBox="0 0 343 30" height="30" preserveAspectRatio="none"><path d="M0 18 Q170 0 343 10 L343 30 L0 30Z" fill="var(--gold)"/><path d="M0 22 Q170 6 343 16 L343 30 L0 30Z" fill="var(--blue)"/><path d="M0 27 Q170 14 343 22 L343 30 L0 30Z" fill="var(--navy)"/></svg>
  <div class="web" style="bottom:4px">www.brighthollowchurch.org</div>
</div>

<!-- Letterhead -->
<div class="label" style="left:389px;top:143px;width:343px">Letterhead</div>
<div class="piece" style="left:389px;top:156px;width:343px;height:492px">
  <div class="faint-circle" style="left:96px;top:200px;width:150px;height:150px"></div>
  <div class="brand" style="left:14px;top:14px">
    <div class="brand-mark" style="width:24px;height:24px"></div>
    <div class="brand-name" style="font-size:8px">Bright Hollow<br>Church</div>
  </div>
  <div class="contact" style="left:262px;top:14px">PO Box 218<br>Millbrook, TX 75400<br>T 555 010 2200<br>F 555 010 2201<br>info@brighthollowchurch.org</div>
  <svg class="swoosh" viewBox="0 0 343 30" height="30" preserveAspectRatio="none"><path d="M0 18 Q170 0 343 10 L343 30 L0 30Z" fill="var(--gold)"/><path d="M0 22 Q170 6 343 16 L343 30 L0 30Z" fill="var(--blue)"/><path d="M0 27 Q170 14 343 22 L343 30 L0 30Z" fill="var(--navy)"/></svg>
  <div class="web" style="bottom:4px">www.brighthollowchurch.org</div>
</div>

<!-- Envelope backs -->
<div class="label" style="left:763px;top:252px;width:413px">Envelopes (Back) Option 1</div>
<div class="piece env-back" style="top:264px">
  <svg width="413" height="140" viewBox="0 0 413 140" style="position:absolute;left:0;top:0"><path d="M0 0 L206 78 L413 0" fill="none" stroke="#d8d8d8" stroke-width="1.5"/><path d="M0 140 L170 64 M413 140 L243 64" stroke="#e4e4e4" stroke-width="1"/></svg>
  <div class="brand" style="left:168px;top:42px"><div class="brand-mark" style="width:18px;height:18px"></div><div class="brand-name" style="font-size:6.5px">Bright Hollow<br>Church</div></div>
</div>

<div class="piece env-back" style="top:372px">
  <svg width="413" height="140" viewBox="0 0 413 140" style="position:absolute;left:0;top:0">
    <defs><linearGradient id="flapBlue" x1="0" y1="0" x2="0" y2="1"><stop offset="0" stop-color="var(--navy)"/><stop offset="1" stop-color="var(--sky)"/></linearGradient></defs>
    <path d="M0 0 L413 0 L413 10 L206 80 L0 10Z" fill="url(#flapBlue)"/>
    <path d="M0 10 L206 80 L413 10" fill="none" stroke="var(--gold)" stroke-width="3"/>
  </svg>
  <div class="env-label" style="top:14px;color:#fff">Envelopes (Back) Option 2</div>
  <div class="brand" style="left:168px;top:52px"><div class="brand-mark" style="width:18px;height:18px"></div><div class="brand-name" style="font-size:6.5px;color:#fff">Bright Hollow<br>Church</div></div>
</div>

<div class="piece env-back" style="top:492px">
  <svg width="413" height="140" viewBox="0 0 413 140" style="position:absolute;left:0;top:0">
    <defs><linearGradient id="flapGold" x1="0" y1="0" x2="0" y2="1"><stop offset="0" stop-color="var(--gold-dark)"/><stop offset="1" stop-color="#ffe27a"/></linearGradient></defs>
    <path d="M0 0 L413 0 L413 10 L206 80 L0 10Z" fill="url(#flapGold)"/>
    <path d="M0 10 L206 80 L413 10" fill="none" stroke="var(--blue)" stroke-width="3"/>
  </svg>
  <div class="env-label" style="top:14px">Envelopes (Back) Option 3</div>
  <div class="brand" style="left:168px;top:52px"><div class="brand-mark" style="width:18px;height:18px"></div><div class="brand-name" style="font-size:6.5px">Bright Hollow<br>Church</div></div>
</div>

</body>
</html>
```